New Innovative Counselling and psychotherapy Service needs Business Card design

Keep it simple and professional. On one side, just company name and logo (perhaps in all blue) and maybe a tag line.

On other side (all white) my name and Qualifications in centre

Industry/Entity Type

Health And Wellness

Contact Information for Business Card

Dara Whelby
Counsellor & Psychotherapist
BSc (Psychol.), BA, Dip. (Couns. & Psych.), PG.Cert (CBT), FGTrK, ONRE

I will also require Mobile no, Email and web site address of which I'll pass on to final designer.

Font styles to use
Sans Serif

Requirements
Must have
• My Logo Only and please use the colours in logo that is in it.
Should not have
• Any other images

```html
<!DOCTYPE html>
<html lang="en">
<head>
<meta charset="utf-8">
<title>Steadfast Grove – Business Card</title>
<link rel="stylesheet" href="https://fonts.googleapis.com/css2?family=Open+Sans:wght@300;400;600&display=swap">
<style>
  :root {
    --page-bg: #d9d9d9;
    --card-dark-top: #3a3a3a;
    --card-dark-bottom: #232323;
    --brand-blue: #4fb0e3;
    --brand-green: #8fcb4f;
    --text-white: #ffffff;
    --text-soft: #d6d6d6;
    --circle-white: #ffffff;
  }
  * { box-sizing: border-box; margin: 0; padding: 0; }
  html, body { width: 1200px; height: 896px; overflow: hidden; }
  body {
    background: var(--page-bg);
    font-family: "Open Sans", Arial, sans-serif;
    display: flex;
    align-items: center;
    justify-content: center;
    gap: 50px;
  }
  .card {
    position: relative;
    width: 520px;
    height: 300px;
    border-radius: 22px;
    overflow: hidden;
    background: linear-gradient(160deg, var(--card-dark-top), var(--card-dark-bottom));
    box-shadow: 0 10px 30px rgba(0,0,0,.25);
  }

  /* Back side */
  .card-back .brand-name {
    position: absolute;
    top: 50%; left: 50%;
    transform: translate(-50%, -60%);
    display: flex; align-items: center; gap: 12px;
    color: var(--brand-blue);
    font-size: 30px; font-weight: 400;
    white-space: nowrap;
  }
  .brand-dot {
    width: 22px; height: 22px; border-radius: 50%;
    background: var(--brand-blue);
    flex-shrink: 0;
  }
  .card-back .web {
    position: absolute; right: 30px; bottom: 26px;
    font-size: 15px; color: var(--text-white);
  }
  .web .web-domain { color: var(--brand-green); }

  /* Front side */
  .badge-rim, .badge {
    position: absolute; border-radius: 50%;
  }
  .badge-rim {
    width: 320px; height: 320px; left: 264px; top: -54px;
    background: var(--brand-blue);
  }
  .badge {
    width: 320px; height: 320px; left: 270px; top: -60px;
    background: var(--circle-white);
  }
  .badge-name {
    position: absolute; left: 284px; top: 86px; width: 222px;
    text-align: center;
    color: var(--brand-blue);
    font-size: 22px; font-weight: 400;
    white-space: nowrap;
  }
  .front-info {
    position: absolute; left: 30px; top: 34px;
  }
  .company {
    display: flex; align-items: center; gap: 8px;
    color: var(--text-white); font-size: 19px; font-weight: 300;
  }
  .company .brand-dot { width: 18px; height: 18px; }
  .person-name {
    margin-top: 14px;
    color: var(--brand-blue);
    font-size: 24px; font-weight: 400; letter-spacing: .5px;
    text-transform: uppercase;
  }
  .role, .credentials {
    color: var(--text-soft); font-size: 12px; line-height: 1.45;
  }
  .role { margin-top: 2px; }
  .contact {
    position: absolute; left: 30px; bottom: 22px;
    list-style: none;
    color: var(--text-white); font-size: 12px; line-height: 1.6;
  }
  .contact li { display: flex; align-items: center; gap: 8px; }
  .contact svg { width: 10px; height: 10px; fill: var(--text-soft); }
</style>
</head>
<body>

  <section class="card card-back" aria-label="Card back">
    <div class="brand-name"><span class="brand-dot"></span>Steadfast Grove</div>
    <p class="web">www.<span class="web-domain">steadfastgrove</span>.com</p>
  </section>

  <section class="card card-front" aria-label="Card front">
    <div class="badge-rim"></div>
    <div class="badge"></div>
    <div class="badge-name">Steadfast Grove</div>

    <div class="front-info">
      <div class="company"><span class="brand-dot"></span>Steadfast Grove</div>
      <h1 class="person-name">Dara Whelby</h1>
      <p class="role">Counsellor &amp; Psychotherapist</p>
      <p class="credentials">BSc (Psychol.), BA, Dip.<br>(Couns. &amp; Psych.), PG.Cert<br>(CBT), FGTrK, ONRE</p>
    </div>

    <ul class="contact">
      <li><svg viewBox="0 0 10 10"><path d="M2 0h2l1 3-1.5 1a6 6 0 0 0 2.5 2.5L7 5l3 1v2c0 1-1 2-2 2C4 10 0 6 0 2c0-1 1-2 2-2z"/></svg>888-555-0147</li>
      <li><svg viewBox="0 0 10 10"><path d="M0 2h10v6H0zM1 3v.3l4 2.7 4-2.7V3L5 5.5z"/></svg>info@steadfastgrove.com</li>
      <li><svg viewBox="0 0 10 10"><circle cx="5" cy="5" r="5"/></svg>www.steadfastgrove.com</li>
    </ul>
  </section>

</body>
</html>
```